Stylish Business Cards Wanted

- DOUBLE SIDED Design Required -

High end, edgy cards for a corporate and personal stylist. Must include logo,
Name: Belinda Harwick
Title: Director and Stylist
telephone : +61 8 7142 5809
email: belinda@theloombriefing.example
website: theloombriefing.example
Tag: Corporate Workwear & Uniform Specialist | Personal Stylist
Would like nice icons for telephone, email, website

Target Market(s)

Businesses wanting stylish uniforms, people wanting stylish wardrobes

Industry/Entity Type

Corporate Workwear Stylist

Contact Information for Business Card

I would like black, white and gold foiling incorporated in the design - possibly a touch of the other colours on my branding guide attached Name: Belinda Harwick Title: Director and Stylist telephone : +61 8 7142 5809 email: belinda@theloombriefing.example website: theloombriefing.example Tag: Corporate Workwear & Uniform Specialist | Personal Stylist Would like nice icons for telephone, email, website

Font styles to use
Other font styles liked:
• Raleway

Colors

Designer to choose colors to be used in the design.

Requirements
Must have
• Gold foil accents

```html
<!DOCTYPE html>
<html lang="en">
<head>
<meta charset="utf-8">
<title>The Loom Briefing – Business Cards</title>
<link rel="stylesheet" href="https://fonts.googleapis.com/css2?family=Arimo:wght@400;700&family=Great+Vibes&family=Raleway:wght@600&display=swap">
<style>
  :root {
    --backdrop: #e4e4e2;
    --card: #262626;
    --card-deep: #1f1f1f;
    --gold: #c9a23f;
    --white: #f4f4f2;
    --emboss: #3a3a3a;
  }
  * { margin: 0; padding: 0; box-sizing: border-box; }
  html, body { width: 1200px; height: 801px; overflow: hidden; }
  body {
    background: var(--backdrop);
    position: relative;
    font-family: "Arimo", Arial, sans-serif;
  }
  .card {
    position: absolute;
    top: 246px;
    width: 540px;
    height: 309px;
    background: var(--card);
    overflow: hidden;
  }
  .card--front { left: 40px; }
  .card--back { left: 620px; background: linear-gradient(135deg, var(--card) 0%, var(--card-deep) 100%); }

  .brand {
    position: absolute;
    top: 46px;
    right: 42px;
    font-family: "Raleway", sans-serif;
    font-weight: 600;
    color: var(--white);
    font-size: 30px;
    line-height: 1.1;
    letter-spacing: 2px;
    text-align: right;
    text-transform: uppercase;
  }

  .holder { position: absolute; left: 30px; top: 150px; }
  .holder__name {
    font-family: "Great Vibes", cursive;
    color: var(--gold);
    font-size: 40px;
    line-height: 1;
  }
  .holder__title {
    color: var(--white);
    font-size: 15px;
    margin-top: 4px;
  }
  .divider {
    position: absolute;
    left: 30px;
    right: 0;
    top: 226px;
    height: 1px;
    background: var(--white);
    opacity: .85;
  }
  .contacts {
    position: absolute;
    left: 30px;
    top: 238px;
    list-style: none;
  }
  .contacts li {
    display: flex;
    align-items: center;
    gap: 8px;
    color: var(--white);
    font-size: 13.5px;
    height: 21px;
  }
  .contacts svg { width: 12px; height: 12px; fill: var(--gold); flex: none; }
  .contacts .accent { color: var(--gold); }

  .brand-mark {
    position: absolute;
    left: 0; right: 0;
    top: 92px;
    text-align: center;
    font-family: "Raleway", sans-serif;
    font-weight: 600;
    color: var(--emboss);
    font-size: 48px;
    line-height: 1.05;
    letter-spacing: 4px;
    text-transform: uppercase;
  }
  .tagline {
    position: absolute;
    left: 0; right: 0;
    bottom: 30px;
    text-align: center;
    color: var(--gold);
    font-weight: 700;
    font-size: 13px;
    letter-spacing: .5px;
  }
</style>
</head>
<body>

<section class="card card--front" aria-label="Card front">
  <div class="brand">The Loom<br>Briefing</div>

  <div class="holder">
    <p class="holder__name">Belinda Harwick</p>
    <p class="holder__title">Director and Stylist</p>
  </div>

  <div class="divider"></div>

  <ul class="contacts">
    <li>
      <svg viewBox="0 0 24 24" aria-hidden="true"><path d="M6.6 10.8a15.1 15.1 0 0 0 6.6 6.6l2.2-2.2a1 1 0 0 1 1-.25 11.4 11.4 0 0 0 3.6.57 1 1 0 0 1 1 1V20a1 1 0 0 1-1 1A17 17 0 0 1 3 4a1 1 0 0 1 1-1h3.5a1 1 0 0 1 1 1c0 1.25.2 2.45.57 3.57a1 1 0 0 1-.25 1z"/></svg>
      +61 8 7142 5809
    </li>
    <li>
      <svg viewBox="0 0 24 24" aria-hidden="true"><path d="M2 5h20v14H2z M3.5 6.5 12 13l8.5-6.5" fill="var(--gold)"/><path d="M3 6l9 7 9-7" fill="none" stroke="#262626" stroke-width="1.6"/></svg>
      belinda@theloombriefing.example
    </li>
    <li>
      <svg viewBox="0 0 24 24" aria-hidden="true"><circle cx="12" cy="12" r="11"/><path d="M1 12h22M12 1c3.5 3 3.5 19 0 22M12 1c-3.5 3-3.5 19 0 22" fill="none" stroke="#262626" stroke-width="1.6"/></svg>
      <span>www.<span class="accent">theloombriefing</span>.example</span>
    </li>
  </ul>
</section>

<section class="card card--back" aria-label="Card back">
  <div class="brand-mark">The Loom<br>Briefing</div>
  <p class="tagline">CORPORATE WORKWEAR | UNIFORM SPECIALIST | PERSONAL STYLIST</p>
</section>

</body>
</html>
```